MV Decor

There is a sample provided with the arabic text of the business card. please copy paste the same text and the same Logo (The two triangles) Just try to incorproate the Brown background attached (you are free to change the colors) Id like the colors to be mainly shades of black and red.

```html
<!DOCTYPE html>
<html lang="ar">
<head>
<meta charset="utf-8">
<title>MV Decor – Business Card</title>
<link rel="stylesheet" href="https://fonts.googleapis.com/css2?family=Aref+Ruqaa:wght@400;700&family=Noto+Kufi+Arabic:wght@400&family=Roboto:wght@500&display=swap">
<style>
  :root {
    --stage: #ece9e6;
    --card-red: #d41f45;
    --card-red-deep: #b8173a;
    --card-red-light: #e2365a;
    --corner-grey: #dcdcdc;
    --ink-white: #ffffff;
    --ink-dark: #1e1e1e;
  }
  * { margin: 0; padding: 0; box-sizing: border-box; }
  html, body {
    width: 1125px;
    height: 1200px;
    overflow: hidden;
    background: var(--stage);
  }
  .canvas {
    position: relative;
    width: 1125px;
    height: 1200px;
  }
  .card {
    position: absolute;
    left: 171px;
    width: 826px;
    height: 472px;
    overflow: hidden;
    box-shadow: 0 3px 8px rgba(0,0,0,0.35);
    color: var(--ink-white);
  }
  .card--front { top: 106px; }
  .card--back { top: 639px; }
  .card__texture {
    position: absolute;
    inset: 0;
    background:
      radial-gradient(ellipse at 40% 35%, var(--card-red-light) 0%, rgba(226,54,90,0) 60%),
      linear-gradient(160deg, var(--card-red) 0%, var(--card-red-deep) 100%);
  }
  .corner {
    position: absolute;
    width: 92px;
    height: 92px;
    background: var(--corner-grey);
  }
  .corner--top-left { top: 0; left: 0; clip-path: polygon(0 0, 100% 0, 0 100%); }
  .corner--bottom-right { bottom: 0; right: 0; clip-path: polygon(100% 0, 100% 100%, 0 100%); }

  .contact {
    position: absolute;
    left: 56px;
    top: 170px;
    width: 232px;
    direction: rtl;
    text-align: right;
  }
  .contact__name {
    font-family: "Aref Ruqaa", serif;
    font-weight: 700;
    font-size: 25px;
    line-height: 1.2;
    white-space: nowrap;
  }
  .contact__role {
    font-family: "Aref Ruqaa", serif;
    font-size: 17px;
    line-height: 1.3;
    margin-left: 40px;
    text-align: center;
  }
  .contact__qualifications {
    list-style: none;
    margin-top: 22px;
    font-family: "Noto Kufi Arabic", sans-serif;
    font-size: 19px;
    line-height: 27px;
    white-space: nowrap;
  }
  .contact__phone {
    position: absolute;
    left: 56px;
    top: 392px;
    display: flex;
    align-items: center;
    gap: 6px;
    font-family: "Roboto", sans-serif;
    font-weight: 500;
    font-size: 21px;
  }
  .contact__phone svg { width: 18px; height: 18px; fill: var(--ink-white); }

  .brand {
    position: absolute;
    left: 564px;
    top: 226px;
    width: 230px;
    text-align: center;
    font-family: "Noto Kufi Arabic", sans-serif;
    font-weight: 400;
    font-size: 38px;
    line-height: 1.2;
    color: var(--ink-white);
    white-space: nowrap;
  }

  .services {
    position: absolute;
    top: 160px;
    list-style: none;
    direction: rtl;
    text-align: right;
    font-family: "Noto Kufi Arabic", sans-serif;
    font-size: 22px;
    line-height: 33px;
    white-space: nowrap;
  }
  .services--right { right: 85px; }
  .services--left { right: 441px; }
  .services li::after {
    content: "";
    display: inline-block;
    width: 9px;
    height: 9px;
    margin-right: 10px;
    border-radius: 50%;
    background: var(--ink-dark);
    vertical-align: middle;
  }
</style>
</head>
<body>
<main class="canvas">
  <section class="card card--front" aria-label="Business card front">
    <div class="card__texture" role="img" aria-label="Red background with a soft mosaic texture"></div>
    <div class="corner corner--top-left"></div>
    <div class="corner corner--bottom-right"></div>

    <div class="contact">
      <p class="contact__name">المهندس / سامي خالد النعيمي</p>
      <p class="contact__role">أستاذ جامعي</p>
      <ul class="contact__qualifications">
        <li>ماجستير تصميم داخلي</li>
        <li>دبلوم عالي فنون بصرية</li>
        <li>أكاديمية الرواق (فيينا)</li>
        <li>استشارات تصميم-فنية</li>
      </ul>
    </div>
    <p class="contact__phone">
      <svg viewBox="0 0 24 24" aria-hidden="true"><path d="M6.6 10.8a15.1 15.1 0 0 0 6.6 6.6l2.2-2.2a1 1 0 0 1 1-.25 11.4 11.4 0 0 0 3.6.57 1 1 0 0 1 1 1V20a1 1 0 0 1-1 1A17 17 0 0 1 3 4a1 1 0 0 1 1-1h3.5a1 1 0 0 1 1 1c0 1.25.2 2.45.57 3.57a1 1 0 0 1-.25 1z"/></svg>
      <span>34527716 / 61294058</span>
    </p>

    <p class="brand">MV Decor</p>
  </section>

  <section class="card card--back" aria-label="Business card back">
    <div class="card__texture" role="img" aria-label="Red background with a soft mosaic texture"></div>
    <ul class="services services--right">
      <li>ماجستير تصميم داخلي</li>
      <li>دبلوم عالي فنون بصرية</li>
      <li>أكاديمية الرواق (فيينا)</li>
      <li>استشارات تصميم-فنية</li>
    </ul>
    <ul class="services services--left">
      <li>ماجستير تصميم داخلي</li>
      <li>دبلوم عالي فنون بصرية</li>
      <li>أكاديمية الرواق (فيينا)</li>
      <li>استشارات تصميم-فنية</li>
    </ul>
  </section>
</main>
</body>
</html>
```